Business Card Design For Marketing Agnecy LVP

Need business card design for marketing agency.

Doug Fenwick
President, CEO
1-555-302-4196
doug@boldpromoperksgroup.example
www.BoldPromoPerksGroup.example

Back Side:
Boost Sales Using Rewards, Incentives & Giveaways
Get A Free Sample Package

Target Market(s)

B2B

Industry/Entity Type

Marketing

Contact Information for Business Card

Doug Fenwick
President, CEO
1-555-302-4196

Back Side:
Get A Free Sample Package

Please note that my current url is OLD DESIGN. I am working on new design and want the business card to match color themes at least on new site. Here is the demo link for new site so you can see the colors I use, etc.

http://layoutcratehub.example/kq/doug/lvp_final/index.html

Requirements
Must have
• Please note that my current url is OLD DESIGN. I am working on new design and want the business card to match color themes at least on new site. Here is the demo link for new site so you can see the colors I use, etc.

Nice to have

Should not have

```html
<!DOCTYPE html>
<html lang="en">
<head>
<meta charset="utf-8">
<title>LVP Business Card</title>
<link href="https://fonts.googleapis.com/css2?family=Montserrat:wght@400;500;600;700&family=Krona+One&display=swap" rel="stylesheet">
<style>
  :root {
    --page: #ffffff;
    --brand-blue: #2a7cc7;
    --ink: #3a3a3a;
    --card-light: #ffffff;
    --card-edge: #e6e6e6;
    --card-dark-top: #4a4a4a;
    --card-dark-bottom: #2c2c2c;
    --on-dark: #ffffff;
  }
  * { margin: 0; padding: 0; box-sizing: border-box; }
  html, body { width: 1200px; height: 840px; overflow: hidden; background: var(--page); }
  body { position: relative; font-family: "Montserrat", Arial, sans-serif; }

  .card {
    position: absolute;
    top: 232px;
    width: 364px;
    height: 364px;
    border-radius: 12px;
    text-align: center;
  }
  .card--front { left: 204px; background: var(--card-light); border: 1px solid var(--card-edge); color: var(--ink); }
  .card--back { left: 632px; background: linear-gradient(160deg, var(--card-dark-top), var(--card-dark-bottom)); color: var(--on-dark); }

  .brand { position: absolute; left: 0; right: 0; top: 42px; color: var(--brand-blue); font-weight: 700; }
  .brand__initials { display: block; font-size: 76px; line-height: 1; letter-spacing: 1px; }
  .brand__name { display: block; margin-top: 12px; font-size: 13px; letter-spacing: 1.6px; }
  .card--back .brand { top: 36px; }

  .person { position: absolute; left: 0; right: 0; top: 206px; }
  .person__name { color: var(--brand-blue); font-size: 18px; font-weight: 600; letter-spacing: 0.6px; }
  .person__title { font-size: 13px; margin-top: 2px; }

  .contact-icons { position: absolute; left: 0; right: 0; top: 262px; display: flex; justify-content: center; gap: 7px; }
  .contact-icons svg { width: 14px; height: 14px; }

  .contact { position: absolute; left: 0; right: 0; top: 280px; font-size: 13px; line-height: 17.6px; }

  .tagline { position: absolute; left: 30px; right: 30px; top: 199px; font-size: 14px; line-height: 18px; font-weight: 400; }

  .cta { position: absolute; left: 14px; top: 245px; width: 335px; height: 60px; }
  .cta svg { position: absolute; inset: 0; width: 100%; height: 100%; }
  .cta__label { position: relative; display: block; line-height: 56px; font-family: "Krona One", "Arial Black", sans-serif; font-size: 12.5px; letter-spacing: 0.4px; color: var(--on-dark); }

  .site { position: absolute; left: 0; right: 0; top: 314px; padding-left: 22px; font-size: 14px; letter-spacing: 0.8px; font-weight: 400; }
</style>
</head>
<body>

<section class="card card--front" aria-label="Card front">
  <div class="brand">
    <span class="brand__initials">LVP</span>
    <span class="brand__name">BOLD PROMO PERKS GROUP</span>
  </div>

  <div class="person">
    <p class="person__name">DOUG FENWICK</p>
    <p class="person__title">President, CEO</p>
  </div>

  <div class="contact-icons" aria-hidden="true">
    <svg viewBox="0 0 14 14"><rect width="14" height="14" rx="2" fill="#2a7cc7"/><path d="M4.3 3.2l1.5-.2.8 2-1 .8c.5 1.1 1.3 1.9 2.4 2.4l.8-1 2 .8-.2 1.5c-.1.5-.5.8-1 .7C6.6 9.8 4.2 7.4 3.6 4.2c-.1-.5.2-.9.7-1z" fill="#fff"/></svg>
    <svg viewBox="0 0 14 14"><rect width="14" height="14" rx="2" fill="#2a7cc7"/><rect x="3" y="4" width="8" height="6" rx="0.8" fill="none" stroke="#fff" stroke-width="1.1"/><path d="M3.3 4.4L7 7.2l3.7-2.8" fill="none" stroke="#fff" stroke-width="1.1"/></svg>
    <svg viewBox="0 0 14 14"><rect width="14" height="14" rx="2" fill="#2a7cc7"/><g fill="none" stroke="#fff" stroke-width="0.9"><circle cx="7" cy="7" r="4"/><ellipse cx="7" cy="7" rx="1.7" ry="4"/><path d="M3 7h8M3.6 5h6.8M3.6 9h6.8"/></g></svg>
  </div>

  <div class="contact">
    <p>1-555-302-4196</p>
    <p>www.BoldPromoPerksGroup.example</p>
    <p>doug@boldpromoperksgroup.example</p>
  </div>
</section>

<section class="card card--back" aria-label="Card back">
  <div class="brand">
    <span class="brand__initials">LVP</span>
    <span class="brand__name">BOLD PROMO PERKS GROUP</span>
  </div>

  <p class="tagline">Boost Sales Using Rewards, Incentives &amp; Giveaways</p>

  <div class="cta">
    <svg viewBox="0 0 335 60" preserveAspectRatio="none" aria-hidden="true">
      <path d="M4 0H331L335 4L328 52L175 52L167 60L159 52L12 52L0 4Z" fill="#2a7cc7"/>
    </svg>
    <span class="cta__label">GET A FREE SAMPLE PACKAGE</span>
  </div>

  <p class="site">www.BoldPromoPerksGroup.example</p>
</section>

</body>
</html>
```